New Bicycle shop business card

Hi!
I'm looking for a business card for my new proffesional bike mechanics shop. This shop is only for fixing broken bikes and not selling bikes.
Peferbly a modern and sleek and modern design.
Colors: black, grey, red, white
Information:
Name: Rijwielwerkplaats Vanhoutte
Shop owner: Bart Vanhoutte & Marieke Segers
Website: www.rijwielwerkplaats-vanhoutte.be
Email: info@rijwielwerkplaats-vanhoutte.be
Phone number: +32471902368
Street adres: Kerkweg 46
9940 Bellebeke
Slogan/shop information: Herstellingen van alle merken.
Logo: see files.
Target Market(s)
People who seek a mechanic to fix or upgrade their bikes.
Contact Information for Business Card
Information:
Website: info@rijwielwerkplaats-vanhoutte.be
9940 Bellebeke
Logo: see files.

```html
<!DOCTYPE html>
<html lang="nl">
<head>
<meta charset="utf-8">
<title>Rijwielwerkplaats Vanhoutte – visitekaartje</title>
<link href="https://fonts.googleapis.com/css2?family=Lato:wght@400;700;900&display=swap" rel="stylesheet">
<style>
  :root {
    --page: #c9c9c9;
    --card-white: #ffffff;
    --brand-red: #e2183e;
    --ink: #1c1c1c;
    --rule: #9a9a9a;
    --shadow: rgba(0,0,0,0.35);
  }
  * { margin: 0; padding: 0; box-sizing: border-box; }
  html, body { width: 1200px; height: 802px; overflow: hidden; }
  body {
    background: var(--page);
    font-family: "Lato", sans-serif;
    position: relative;
  }
  .card {
    position: absolute;
    top: 274px;
    width: 443px;
    height: 265px;
    box-shadow: 2px 3px 5px var(--shadow);
    overflow: hidden;
  }
  .card--front { left: 136px; background: var(--card-white); }
  .card--back { left: 624px; }

  /* front */
  .brand {
    position: absolute;
    left: 14px;
    top: 90px;
    width: 168px;
    text-align: center;
    color: var(--ink);
    font-weight: 900;
    font-size: 14.5px;
    line-height: 1.25;
    letter-spacing: 0.5px;
    text-transform: uppercase;
  }
  .brand__dot {
    display: block;
    width: 26px; height: 26px;
    margin: 0 auto 10px;
    border-radius: 50%;
    background: var(--brand-red);
  }
  .divider {
    position: absolute;
    left: 190px; top: 71px;
    width: 1px; height: 123px;
    background: var(--rule);
  }
  .contact {
    position: absolute;
    left: 203px; top: 72px;
    color: var(--ink);
    font-size: 11.5px;
    line-height: 1.4;
  }
  .contact__names {
    color: var(--brand-red);
    font-weight: 700;
    font-size: 10.5px;
    text-transform: uppercase;
  }
  .contact__role { margin-bottom: 5px; }
  .contact__line { display: flex; align-items: center; gap: 4px; white-space: nowrap; font-size: 11px; }
  .contact__line svg { width: 9px; height: 9px; flex: none; fill: var(--brand-red); }
  .contact__address { margin-top: 8px; }

  /* back */
  .back__field {
    position: absolute; inset: 0;
    background: linear-gradient(135deg, #e31a40, #dc143a);
  }
  .back__text {
    position: absolute; inset: 0;
    display: flex; flex-direction: column; align-items: center; justify-content: center;
    color: #fff; text-align: center;
    padding-bottom: 10px;
  }
  .back__name {
    font-weight: 900; font-size: 20px; line-height: 1.2;
    letter-spacing: 1px; text-transform: uppercase;
  }
  .back__slogan {
    margin-top: 12px;
    font-size: 12.5px; text-transform: uppercase;
  }
</style>
</head>
<body>
  <section class="card card--front">
    <div class="brand">
      <span class="brand__dot"></span>
      Rijwielwerkplaats<br>Vanhoutte
    </div>
    <div class="divider"></div>
    <div class="contact">
      <p class="contact__names">Bart Vanhoutte &amp; Marieke Segers</p>
      <p class="contact__role">Owner</p>
      <p class="contact__line">
        <svg viewBox="0 0 10 10" aria-hidden="true"><path d="M1 3c0-1 1-2 4-2s4 1 4 2v1H7V3H3v1H1z M2 5h6l1 4H1z"/></svg>
        +32471902368
      </p>
      <p class="contact__line">
        <svg viewBox="0 0 10 10" aria-hidden="true"><path d="M0 2h10v6H0z M0 2l5 4 5-4" stroke="#fff" stroke-width="0.8"/></svg>
        info@rijwielwerkplaats-vanhoutte.be
      </p>
      <p class="contact__line">
        <svg viewBox="0 0 10 10" aria-hidden="true"><circle cx="5" cy="5" r="5"/><circle cx="5" cy="5" r="2" fill="#fff"/></svg>
        www.rijwielwerkplaats-vanhoutte.be
      </p>
      <p class="contact__address">Kerkweg 46<br>9940 Bellebeke</p>
    </div>
  </section>

  <section class="card card--back">
    <div class="back__field" role="img" aria-label="Rode achtergrond met herhalend merkpatroon"></div>
    <div class="back__text">
      <p class="back__name">Rijwielwerkplaats<br>Vanhoutte</p>
      <p class="back__slogan">Herstellingen van alle merken</p>
    </div>
  </section>
</body>
</html>
```